Postcard for dumpster rental business

We need an attractive post card to entice other businesses to use our dumpster rental service. This is a business to business situation.
Target Market(s)
Roofing, property restoration and remodeling contractors
Industry/Entity Type
Dumpster rentals
Font styles to use
Sans Serif
Colors
0054AA
0677BA
7BADD7
CADEEF
E8F1F8
Requirements
Must have
- 42goskips.net Dumpster rental Easy online booking Logo Guaranteed On Time Delivery (as a badge or button?) QR Code Picture of our dumpster (see website)
Nice to have
- Call to action "Order now!"

```html
<!DOCTYPE html>
<html lang="en">
<head>
<meta charset="utf-8">
<title>42go Skip Rental – Postcard</title>
<link rel="stylesheet" href="https://fonts.googleapis.com/css2?family=Montserrat:wght@300;400;500;700;800&family=Poppins:wght@400;500;600;700&display=swap">
<style>
  :root{
    --blue:#2c7bc0;
    --blue-deep:#0054AA;
    --blue-mid:#0677BA;
    --blue-soft:#7BADD7;
    --blue-pale:#CADEEF;
    --blue-mist:#E8F1F8;
    --orange:#ff7300;
    --ink:#1b1b1b;
    --white:#ffffff;
    --stamp:#ececec;
    --page:#f4f4f4;
  }
  *{box-sizing:border-box;margin:0;padding:0}
  html,body{width:1200px;height:2400px;overflow:hidden;background:var(--page)}
  body{position:relative;font-family:"Montserrat",sans-serif;color:var(--ink)}

  .postcard{position:absolute;left:50px;width:1100px;height:733px;overflow:hidden;background:var(--white);box-shadow:0 6px 18px rgba(0,0,0,.25)}
  .postcard--front{top:417px}
  .postcard--back{top:1250px}

  /* front */
  .front-sky{position:absolute;left:0;top:0;width:1100px;height:340px;background:var(--blue)}
  .hero-photo{position:absolute;left:370px;top:0;width:730px;height:653px;
    background:radial-gradient(ellipse 60% 55% at 62% 60%,rgba(240,120,20,.9) 0%,rgba(240,120,20,.55) 55%,rgba(240,120,20,0) 100%)}
  .brand-badge{position:absolute;left:740px;top:-70px;width:400px;height:400px}
  .brand-lockup{position:absolute;left:0;top:0;width:100%;display:flex;align-items:center;justify-content:center;gap:10px}
  .brand-mark{width:28px;height:28px;background:var(--blue-deep);flex:none}
  .brand-name{font-family:"Montserrat",sans-serif;font-weight:800;color:var(--blue-deep);font-size:26px;letter-spacing:.3px;white-space:nowrap}
  .front-brand{top:160px;width:380px}

  .headline{position:absolute;left:49px;top:46px;color:var(--white);font-size:68px;line-height:62px;text-transform:uppercase}
  .headline .light{font-weight:400;display:block;letter-spacing:-1px}
  .headline .bold{font-weight:800;display:block;letter-spacing:-1px}

  .intro{position:absolute;left:51px;top:360px;width:285px;font-size:14.3px;line-height:16.5px;color:#222}

  .van{position:absolute;background:linear-gradient(100deg,#d92a2a 0%,#e46b6b 60%,#f2eeee 100%);border-radius:14px}
  .guarantee{position:absolute;background:var(--orange);border-radius:0 42px 42px 0;color:var(--white);display:flex;flex-direction:column;justify-content:center;text-transform:uppercase;line-height:1}
  .guarantee strong{font-weight:800;letter-spacing:.5px}
  .guarantee span{font-weight:400}

  .front .van{left:46px;top:520px;width:176px;height:106px}
  .front .guarantee{left:226px;top:526px;width:256px;height:76px;padding-left:28px}
  .front .guarantee strong{font-size:28px}
  .front .guarantee span{font-size:21px;margin-top:3px}

  .contact-bar{position:absolute;left:0;bottom:0;width:1100px;height:80px;background:var(--ink)}
  .order-tab{position:absolute;left:63px;top:640px;width:230px;height:66px;border-radius:10px;color:var(--white);font-weight:700;font-size:30px;display:flex;align-items:center;justify-content:center;letter-spacing:.3px}
  .order-tab--blue{background:var(--blue-mid)}
  .order-tab--orange{background:var(--orange)}
  .contact{position:absolute;top:670px;display:flex;align-items:center;gap:12px;color:var(--white);white-space:nowrap}
  .contact svg{width:30px;height:30px;flex:none}
  .contact--phone{left:336px;font-family:"Poppins",sans-serif;font-weight:600;font-size:32px}
  .contact--web{left:636px;font-family:"Poppins",sans-serif;font-weight:400;font-size:27px;letter-spacing:1px}

  /* back */
  .back-panel{position:absolute;left:0;top:0;width:552px;height:655px}
  .service-title{position:absolute;left:51px;top:50px;font-family:"Poppins",sans-serif;font-weight:700;font-size:28px;color:var(--white)}
  .service-copy{position:absolute;left:51px;width:446px;font-family:"Montserrat",sans-serif;font-size:13.3px;line-height:16.3px;color:var(--white);text-align:justify}
  .service-copy--one{top:96px}
  .service-copy--two{top:224px}
  .dumpster-shot{position:absolute;left:108px;top:368px;width:320px;height:120px;
    background:radial-gradient(ellipse 50% 50% at 50% 50%,rgba(246,122,18,.95) 0%,rgba(246,122,18,.6) 60%,rgba(246,122,18,0) 100%)}
  .price-box{position:absolute;left:70px;top:514px;width:414px;height:100px;color:var(--white);text-align:center}
  .price-box svg{position:absolute;left:0;top:0}
  .price-label{position:absolute;left:0;top:-4px;width:100%;font-size:25px;font-weight:400;line-height:30px;white-space:nowrap}
  .price{position:absolute;left:0;top:32px;width:100%;font-family:"Poppins",sans-serif;font-weight:700;font-size:50px;line-height:56px}
  .price sup{font-size:28px;vertical-align:top;line-height:36px}
  .back-brand{position:absolute;left:600px;top:90px;width:300px}
  .stamp{position:absolute;left:943px;top:58px;width:105px;height:105px;background:var(--stamp)}
  .back .van{left:490px;top:528px;width:210px;height:120px}
  .back .guarantee{left:690px;top:545px;width:330px;height:84px;padding-left:40px}
  .back .guarantee strong{font-size:33px}
  .back .guarantee span{font-size:25px;margin-top:3px}
</style>
</head>
<body>

<section class="postcard postcard--front front" aria-label="Postcard front">
  <div class="front-sky"></div>
  <div class="hero-photo" role="img" aria-label="Photo of a worker throwing scrap into large orange roll-off dumpsters"></div>

  <div class="brand-badge">
    <svg width="400" height="400" viewBox="0 0 400 400" aria-hidden="true">
      <circle cx="190" cy="180" r="190" fill="var(--blue-mid)"/>
      <circle cx="190" cy="180" r="170" fill="var(--blue-soft)"/>
      <circle cx="190" cy="180" r="150" fill="var(--white)"/>
    </svg>
    <div class="brand-lockup front-brand">
      <span class="brand-mark"></span>
      <span class="brand-name">42go Skip Rental</span>
    </div>
  </div>

  <h1 class="headline">
    <span class="light">Dumpster</span>
    <span class="light">Rental and</span>
    <span class="bold">Removal</span>
    <span class="bold">Services</span>
  </h1>

  <p class="intro">42go Skip Rental is locally owned and operated by a small-business team with a reputation that spans over 30 years. Our competitive prices and high standards allow us to offer comprehensive, professional, and personalized customer-service to meet your practical and financial needs.</p>

  <div class="van" role="img" aria-label="Illustration of a red delivery van"></div>
  <div class="guarantee"><strong>Guaranteed</strong><span>On time delivery</span></div>

  <div class="contact-bar"></div>
  <div class="order-tab order-tab--blue">ORDER NOW</div>
  <div class="contact contact--phone">
    <svg viewBox="0 0 24 24" aria-hidden="true"><path fill="var(--orange)" d="M6.6 10.8a15.1 15.1 0 0 0 6.6 6.6l2.2-2.2a1 1 0 0 1 1-.25 11.4 11.4 0 0 0 3.6.57 1 1 0 0 1 1 1V20a1 1 0 0 1-1 1A17 17 0 0 1 3 4a1 1 0 0 1 1-1h3.5a1 1 0 0 1 1 1c0 1.25.2 2.45.57 3.57a1 1 0 0 1-.25 1z"/></svg>
    <span>(555) 014-2290</span>
  </div>
  <div class="contact contact--web">
    <svg viewBox="0 0 24 24" aria-hidden="true"><g fill="none" stroke="var(--orange)" stroke-width="2"><circle cx="12" cy="12" r="9"/><ellipse cx="12" cy="12" rx="4" ry="9"/><path d="M3 12h18M4.5 7.5h15M4.5 16.5h15"/></g></svg>
    <span>www.42goskips.net</span>
  </div>
</section>

<section class="postcard postcard--back back" aria-label="Postcard back">
  <svg class="back-panel" viewBox="0 0 552 655" aria-hidden="true">
    <defs>
      <linearGradient id="panelBlue" x1="0" y1="0" x2="0" y2="1">
        <stop offset="0" stop-color="var(--blue)"/>
        <stop offset="1" stop-color="#215f9f"/>
      </linearGradient>
    </defs>
    <rect width="552" height="655" fill="url(#panelBlue)"/>
    <path d="M0 0H552V355C470 400 380 410 290 405C170 400 60 380 0 300Z" fill="var(--orange)"/>
  </svg>

  <h2 class="service-title">Our rental service</h2>
  <p class="service-copy service-copy--one">Lorem ipsum dolor sit amet, consectetur adipiscing elit. Integer sit amet ex viverra, laoreet nisl nec, aliquam urna. Orci varius natoque penatibus et magnis dis parturient montes, nascetur ridiculus mus. Nulla commodo quam ac nulla finibus, sit amet sodales quam vestibulum. Donec tincidunt, turpis nec venenatis pharetra, quam eros malesuada ipsum, non maximus massa metus sed orci. Donec a leo laoreet, suscipit metus et, tincidunt mauris.</p>
  <p class="service-copy service-copy--two">Lorem ipsum dolor sit amet, consectetur adipiscing elit. Integer sit amet ex viverra, laoreet nisl nec, aliquam urna. Orci varius natoque penatibus et magnis dis parturient montes, nascetur ridiculus mus. Nulla commodo quam ac nulla finibus, aliquam urna. Orci varius natoque penatibus et magnis dis parturient montes, nascetur ridiculus mus. Nulla commodo quam ac nulla finibus.</p>

  <div class="dumpster-shot" role="img" aria-label="Photo of an orange 10 yard dumpster"></div>

  <div class="price-box">
    <svg width="414" height="100" viewBox="0 0 414 100" aria-hidden="true">
      <path d="M74 11H2V98H412V11H340" fill="none" stroke="var(--white)" stroke-width="2" stroke-dasharray="6 4"/>
    </svg>
    <span class="price-label">10 YARD DUMPSTER</span>
    <div class="price"><sup>$</sup>318.00</div>
  </div>

  <div class="back-brand">
    <div class="brand-lockup">
      <span class="brand-mark"></span>
      <span class="brand-name">42go Skip Rental</span>
    </div>
  </div>
  <div class="stamp"></div>

  <div class="guarantee"><strong>Guaranteed</strong><span>On time delivery</span></div>
  <div class="van" role="img" aria-label="Illustration of a red delivery van"></div>

  <div class="contact-bar"></div>
  <div class="order-tab order-tab--orange">ORDER NOW</div>
  <div class="contact contact--phone">
    <svg viewBox="0 0 24 24" aria-hidden="true"><path fill="var(--orange)" d="M6.6 10.8a15.1 15.1 0 0 0 6.6 6.6l2.2-2.2a1 1 0 0 1 1-.25 11.4 11.4 0 0 0 3.6.57 1 1 0 0 1 1 1V20a1 1 0 0 1-1 1A17 17 0 0 1 3 4a1 1 0 0 1 1-1h3.5a1 1 0 0 1 1 1c0 1.25.2 2.45.57 3.57a1 1 0 0 1-.25 1z"/></svg>
    <span>(555) 014-2290</span>
  </div>
  <div class="contact contact--web">
    <svg viewBox="0 0 24 24" aria-hidden="true"><g fill="none" stroke="var(--orange)" stroke-width="2"><circle cx="12" cy="12" r="9"/><ellipse cx="12" cy="12" rx="4" ry="9"/><path d="M3 12h18M4.5 7.5h15M4.5 16.5h15"/></g></svg>
    <span>www.42goskips.net</span>
  </div>
</section>

</body>
</html>
```